House-share and Room Rental Website (With Focus on the Bedroom Landing Page)

Looking for website design for our House-share (executive accommodation) and room rental business.

Our company name is: Lodgivo could also be written as LodGivo or lodgivo. Either is fine .. just looking for a nice clean catchy logo to go with the design.

EXAMPLES
These are examples of other websites in this field that are doing well. this is a kind of baseline.
https://nestpartners-example.com.au/
https://www.bunkora-example.com/
https://www.dwelzy-example.com/
https://www.habiquo-example.net/
https://www.cohabiscout-example.com.au/

Our business model is to rent rooms to people looking for high-quality accommodation. We fill the gap between those looking to rent rooms and those with rooms to rent. However, our model is slightly different from those already on the market as we looking to fill a massive gap in the market delivering upmarket rooms for rent.(Executive Accommodation) also in the back end will be coupled with a self management process in the back end.

We offer executive style accommodation that stands out above the rest. With special extras like fire safety.. and management processes that create happier homes. We are looking for a web design package that can help us grow and scale our business. We need a design that is captivating

Our MAIN focus is having a room landing page that stands out from the rest... The core of our business will rely on the promotion of the rooms in a share house... so the whole design relies on the BEDROOM landing page to drive results.

Target Market(s)

We have 2 markets we are aiming at ... the first market is people offering rooms to rent who want the highest rental return. The second market is people looking to rent safe, high-quality rooms, in houses that are well managed and looked after.

Industry/Entity Type

Share Economy

Logo Text

LodGivo

Number of Pages Required

5+ page

Font styles to use
Sans Serif

Colors
3276b5

Requirements
Must have
• A messaging system whereby we can create direct communication between those offering rooms and those looking for rooms.
• A call to action that says " Schedule an Inspection"
• Landing page for promoting rooms
• A home page for showing stock.
• Profile page for those selling rooms
• Profile page for those looking for rooms.
• A scheduling calendar for booking inspections
Nice to have
• Pages where new residents can lock in a room.. pay bond and rents.. and sign contracts
• Notifications
• SMS capabilities in the backend.
Should not have
• No script or handwriting fonts.

```html
<!DOCTYPE html>
<html lang="en">
<head>
<meta charset="utf-8">
<title>Lodgivo – Executive Accommodation</title>
<link href="https://fonts.googleapis.com/css2?family=Montserrat:wght@400;500;600;700&family=Lato:wght@400;700&display=swap" rel="stylesheet">
<style>
:root{
  --blue:#1474cc;
  --blue-dark:#0f5fa8;
  --ink:#1d1d1d;
  --text:#555;
  --muted:#888;
  --line:#e2e2e2;
  --footer:#1e1e1e;
  --footer-field:#3a3a3a;
  --white:#fff;
  --btn-dark:#3b3b3b;
}
*{box-sizing:border-box;margin:0;padding:0}
html,body{width:1200px;height:4286px;overflow:hidden}
body{font-family:"Lato",Arial,sans-serif;color:var(--text);background:var(--white);position:relative}
h1,h2,h3,h4{font-family:"Montserrat",Arial,sans-serif;color:var(--ink)}

/* header */
.site-header{position:absolute;top:0;left:0;width:1200px;height:94px;display:flex;align-items:center;padding:0 64px}
.menu-grid{display:grid;grid-template-columns:repeat(3,5px);gap:4px}
.menu-grid span{width:5px;height:5px;background:var(--ink)}
.lang{margin-left:26px;display:flex;align-items:center;gap:6px;font-size:13px;color:var(--ink)}
.lang i{width:18px;height:12px;background:linear-gradient(#b33 0 50%,#eee 50%)}
.brand{position:absolute;left:50%;transform:translateX(-50%);display:flex;align-items:center;gap:10px}
.brand-dot{width:34px;height:34px;border-radius:50%;background:var(--blue)}
.brand-name{font-family:"Montserrat",sans-serif;font-weight:700;font-size:26px;color:var(--blue);line-height:1}
.brand-tag{font-size:10px;color:var(--ink);letter-spacing:.5px}
.header-actions{margin-left:auto;display:flex;gap:12px}
.btn{font-family:"Montserrat",sans-serif;font-size:13px;font-weight:600;border-radius:4px;padding:9px 16px;display:inline-block}
.btn-primary{background:var(--blue);color:var(--white)}
.btn-outline{border:1px solid #bbb;color:var(--ink)}

/* hero */
.hero{position:absolute;top:94px;left:0;width:1200px;height:552px;background:linear-gradient(160deg,#4a3a2c 0%,#7b6652 35%,#b9a58c 60%,#5a4736 100%)}
.hero-title{position:absolute;top:262px;width:100%;text-align:center;color:var(--white);font-family:"Montserrat",sans-serif;font-weight:500;font-size:31px;line-height:40px}
.hero-arrow{position:absolute;top:268px;color:var(--white);font-size:22px}

/* search */
.search{position:absolute;top:646px;left:0;width:1200px;height:160px;background:var(--blue)}
.field{position:absolute;top:50px}
.field label{display:block;font-size:12px;color:var(--white);margin-bottom:6px}
.field .box{height:32px;background:var(--white);border-radius:2px;font-size:12px;color:#666;padding:0 10px;display:flex;align-items:center;justify-content:space-between}
.search-btn{position:absolute;left:1089px;top:70px;width:46px;height:32px;background:var(--btn-dark);border-radius:2px;display:flex;align-items:center;justify-content:center}

/* recommended */
.section-title{position:absolute;width:100%;text-align:center;font-weight:500;font-size:34px}
.tabs{position:absolute;top:938px;left:0;width:1200px;display:flex;justify-content:center;gap:62px}
.tab{width:80px;text-align:center;font-size:17px;color:var(--ink)}
.tab svg{display:block;margin:0 auto 8px;height:46px}
.tab.active{color:var(--blue)}

.room-card{position:absolute;width:340px;height:408px;border:1px solid var(--line);background:var(--white);box-shadow:0 2px 6px rgba(0,0,0,.06)}
.room-photo{position:absolute;top:8px;left:8px;width:322px;height:214px}
.room-strip{position:absolute;top:222px;left:8px;width:322px;height:54px;background:var(--blue);color:var(--white);font-size:14px;line-height:18px;padding:9px 10px}
.price{position:absolute;right:0;top:-6px;width:72px;height:66px;background:var(--blue-dark);color:var(--white);font-family:"Montserrat",sans-serif;font-weight:700;font-size:22px;display:flex;align-items:center;justify-content:center;clip-path:polygon(16% 0,100% 0,100% 100%,16% 100%,0 50%)}
.room-meta{position:absolute;top:290px;left:16px;font-size:12.5px;color:var(--ink);font-weight:700}
.room-desc{position:absolute;top:314px;left:16px;width:300px;font-size:12.5px;line-height:17px}
.room-more{position:absolute;top:362px;left:16px;font-size:12.5px;color:var(--ink);text-decoration:underline}

.view-more{position:absolute;left:540px;width:130px;height:26px;background:var(--blue);color:var(--white);font-size:12px;border-radius:3px;display:flex;align-items:center;justify-content:center;font-family:"Montserrat",sans-serif}

/* feature */
.feature{position:absolute;top:2054px;left:0;width:1200px;height:517px;background:linear-gradient(90deg,#5a3a26 0%,#c9b59a 40%,#e8dccb 70%,#8d7558 100%)}
.feature-card{position:absolute;top:60px;left:111px;width:412px;height:377px;background:var(--blue);color:var(--white);padding:32px 42px}
.feature-loc{font-size:15px}
.feature-name{color:var(--white);font-weight:600;font-size:33px;line-height:40px;margin-top:8px;white-space:nowrap}
.feature-amount{font-family:"Montserrat",sans-serif;font-weight:700;font-size:21px;margin-top:6px}
.feature-specs{font-family:"Montserrat",sans-serif;font-weight:600;font-size:15px;line-height:22px;margin-top:12px}
.feature-text{font-size:14px;line-height:19px;margin-top:18px}
.feature-btn{display:inline-block;margin-top:20px;background:var(--btn-dark);color:var(--white);font-family:"Montserrat",sans-serif;font-weight:600;font-size:13px;padding:8px 30px;border-radius:3px}
.feature-nav{position:absolute;right:20px;bottom:16px;font-size:22px}

/* amenities */
.amenity{position:absolute;top:2726px;width:180px;text-align:center}
.amenity .circle{width:88px;height:88px;border-radius:50%;background:var(--blue);margin:0 auto;display:flex;align-items:center;justify-content:center}
.amenity h4{font-weight:500;font-size:19px;margin-top:14px}
.amenity p{font-size:12.5px;line-height:17px;margin-top:14px;padding:0 22px}
.amenity .go{width:24px;height:24px;border:1.5px solid var(--ink);border-radius:50%;margin:18px auto 0;display:flex;align-items:center;justify-content:center}

/* blogs */
.blog-card{position:absolute;top:3120px;width:326px;height:400px;background:var(--white);box-shadow:0 2px 8px rgba(0,0,0,.1)}
.blog-photo{height:228px}
.blog-badge{position:absolute;top:200px;left:135px;width:56px;height:56px;border-radius:50%;background:var(--blue);border:4px solid var(--white);display:flex;align-items:center;justify-content:center}
.blog-card h4{position:absolute;top:256px;left:28px;font-weight:500;font-size:22px}
.blog-date{position:absolute;top:260px;right:24px;font-size:13px;color:var(--ink)}
.blog-card p{position:absolute;top:296px;left:28px;width:270px;font-size:13px;line-height:17px}
.blog-foot{position:absolute;top:352px;left:28px;right:24px;display:flex;align-items:center;font-size:13px;color:var(--ink)}
.blog-foot .read{text-decoration:underline;margin-right:auto}
.blog-foot span.stat{display:flex;align-items:center;gap:5px;margin-left:18px;color:var(--blue)}
.blog-foot span.stat b{color:var(--ink);font-weight:400}

/* newsletter */
.newsletter-sub{position:absolute;top:3705px;width:100%;text-align:center;font-size:13px;color:var(--ink)}
.newsletter-form{position:absolute;top:3746px;left:329px;width:580px;height:40px;display:flex}
.newsletter-form .input{flex:1;background:#f3f3f3;font-size:13px;color:#999;padding:0 28px;display:flex;align-items:center}
.newsletter-form .submit{width:150px;background:var(--blue);color:var(--white);font-size:14px;display:flex;align-items:center;justify-content:center}

/* footer */
.site-footer{position:absolute;top:3871px;left:0;width:1200px;height:352px;background:var(--footer);color:#ddd}
.f-col{position:absolute;top:74px}
.f-col h4{color:var(--white);font-weight:500;font-size:16px;margin-bottom:24px}
.f-brand{display:flex;align-items:center;gap:10px}
.f-brand .brand-dot{width:30px;height:30px}
.f-brand .brand-name{color:var(--white);font-size:24px}
.f-about{font-size:14px;line-height:20px;color:var(--white);margin-top:22px;width:220px}
.socials{display:flex;gap:10px;margin-top:22px}
.socials span{width:24px;height:24px;border-radius:50%;background:var(--blue)}
.socials span+span{background:transparent;border:1.5px solid #ccc}
.links li{list-style:none;font-size:13px;line-height:21px}
.contact-row{display:flex;gap:14px;font-size:14px;line-height:20px;margin-bottom:12px}
.qc-row{display:flex;gap:4px}
.qc-field{background:var(--footer-field);height:30px;font-size:12px;color:#ddd;padding:0 10px;display:flex;align-items:center}
.qc-send{margin:14px 0 0 108px;width:128px;height:28px;background:var(--blue);color:var(--white);font-size:14px;display:flex;align-items:center;justify-content:center}

.bottom-bar{position:absolute;top:4223px;left:0;width:1200px;height:63px;background:var(--blue);color:var(--white);font-size:13px;display:flex;align-items:center;padding:0 64px}
.cards{margin-left:auto;display:flex;gap:8px}
.cards span{width:36px;height:22px;background:var(--white);border-radius:3px}
</style>
</head>
<body>

<header class="site-header">
  <div class="menu-grid"><span></span><span></span><span></span><span></span><span></span><span></span><span></span><span></span><span></span></div>
  <div class="lang"><i></i>Eng ▾</div>
  <div class="brand">
    <span class="brand-dot"></span>
    <div><div class="brand-name">Lodgivo</div><div class="brand-tag">Executive Accommodation</div></div>
  </div>
  <div class="header-actions"><span class="btn btn-primary">Post Your Room</span><span class="btn btn-outline">Log in</span></div>
</header>

<section class="hero" role="img" aria-label="Photo of a luxurious timber-beamed bedroom with a large bed and lounge">
  <span class="hero-arrow" style="left:40px">‹</span>
  <span class="hero-arrow" style="right:40px">›</span>
  <h1 class="hero-title">Let us Find Your Perfect<br>Room For Rent</h1>
</section>

<section class="search">
  <div class="field" style="left:69px;width:274px"><label>Where</label><div class="box">Anywhere <svg width="12" height="12"><circle cx="6" cy="5" r="4" fill="none" stroke="#888"/></svg></div></div>
  <div class="field" style="left:363px;width:174px"><label>Check in</label><div class="box">Select date <svg width="14" height="12"><rect x="1" y="1" width="12" height="10" fill="none" stroke="#888"/></svg></div></div>
  <div class="field" style="left:557px;width:174px"><label>Check out</label><div class="box">Select date <svg width="14" height="12"><rect x="1" y="1" width="12" height="10" fill="none" stroke="#888"/></svg></div></div>
  <div class="field" style="left:751px;width:175px"><label>Category</label><div class="box">Room For Rent <span>▾</span></div></div>
  <div class="field" style="left:946px;width:128px"><label>Rooms</label><div class="box">02 <span>▾</span></div></div>
  <div class="search-btn"><svg width="16" height="16"><circle cx="7" cy="7" r="5" fill="none" stroke="#fff" stroke-width="2"/><line x1="11" y1="11" x2="15" y2="15" stroke="#fff" stroke-width="2"/></svg></div>
</section>

<h2 class="section-title" style="top:864px">Recommended for you</h2>
<nav class="tabs">
  <div class="tab"><svg viewBox="0 0 40 40" width="40"><g fill="#222"><rect x="2" y="2" width="8" height="8"/><rect x="16" y="2" width="8" height="8"/><rect x="30" y="2" width="8" height="8"/><rect x="2" y="16" width="8" height="8"/><rect x="16" y="16" width="8" height="8"/><rect x="30" y="16" width="8" height="8"/><rect x="2" y="30" width="8" height="8"/><rect x="16" y="30" width="8" height="8"/><rect x="30" y="30" width="8" height="8"/></g></svg>All</div>
  <div class="tab"><svg viewBox="0 0 44 40" width="44"><g fill="#222"><rect x="4" y="18" width="36" height="12"/><rect x="4" y="10" width="14" height="8"/><rect x="26" y="10" width="14" height="8"/><rect x="2" y="30" width="4" height="8"/><rect x="38" y="30" width="4" height="8"/></g></svg>Roomate</div>
  <div class="tab active"><svg viewBox="0 0 40 46" width="40"><rect x="8" y="2" width="24" height="42" fill="none" stroke="#1474cc" stroke-width="3"/><polygon points="8,2 26,8 26,46 8,44" fill="#1474cc"/></svg>Room</div>
  <div class="tab"><svg viewBox="0 0 44 44" width="44"><polygon points="22,2 42,20 36,20 36,42 8,42 8,20 2,20" fill="#222"/><rect x="18" y="28" width="8" height="14" fill="#fff"/></svg>House</div>
  <div class="tab"><svg viewBox="0 0 44 44" width="44"><polygon points="22,2 42,20 36,20 36,42 8,42 8,20 2,20" fill="#222"/><circle cx="22" cy="26" r="5" fill="#fff"/><rect x="15" y="32" width="14" height="8" fill="#fff"/></svg>Tenant</div>
</nav>

<article class="room-card" style="left:57px;top:1057px"><div class="room-photo" role="img" aria-label="Photo of a bedroom with ornate carved headboard" style="background:linear-gradient(160deg,#5a3a2a,#c8b3a0 60%,#efe6da)"></div><div class="room-strip">25 Harbourview Road, Elmsvale<br>New South Wales<span class="price">$250</span></div><div class="room-meta">▪ 2Guests / 2Rooms / 4Bedrooms / 3Bath</div><p class="room-desc">Lorem Ipsum is simply dummy text of the printing and typesetting industry.</p><span class="room-more">More Details</span></article>
<article class="room-card" style="left:429px;top:1057px"><div class="room-photo" role="img" aria-label="Photo of a bright bedroom with padded wall and curtains" style="background:linear-gradient(160deg,#8a7660,#d9cbb8 55%,#f3ede4)"></div><div class="room-strip">25 Harbourview Road, Elmsvale<br>New South Wales<span class="price">$250</span></div><div class="room-meta">▪ 2Guests / 2Rooms / 4Bedrooms / 3Bath</div><p class="room-desc">Lorem Ipsum is simply dummy text of the printing and typesetting industry.</p><span class="room-more">More Details</span></article>
<article class="room-card" style="left:803px;top:1057px"><div class="room-photo" role="img" aria-label="Photo of a spacious bedroom with blue accents" style="background:linear-gradient(160deg,#6b5a4a,#b7a898 50%,#5b6f8a)"></div><div class="room-strip">25 Harbourview Road, Elmsvale<br>New South Wales<span class="price">$250</span></div><div class="room-meta">▪ 2Guests / 2Rooms / 4Bedrooms / 3Bath</div><p class="room-desc">Lorem Ipsum is simply dummy text of the printing and typesetting industry.</p><span class="room-more">More Details</span></article>
<article class="room-card" style="left:57px;top:1500px"><div class="room-photo" role="img" aria-label="Photo of a bedroom with blue feature wall" style="background:linear-gradient(160deg,#3e5f80,#d8d2c8 55%,#f0ece6)"></div><div class="room-strip">25 Harbourview Road, Elmsvale<br>New South Wales<span class="price">$250</span></div><div class="room-meta">▪ 2Guests / 2Rooms / 4Bedrooms / 3Bath</div><p class="room-desc">Lorem Ipsum is simply dummy text of the printing and typesetting industry.</p><span class="room-more">More Details</span></article>
<article class="room-card" style="left:429px;top:1500px"><div class="room-photo" role="img" aria-label="Photo of a bedroom with ceiling fan and pale blue ceiling" style="background:linear-gradient(180deg,#a9cde0,#e6e0d6 50%,#7a5e48)"></div><div class="room-strip">25 Harbourview Road, Elmsvale<br>New South Wales<span class="price">$250</span></div><div class="room-meta">▪ 2Guests / 2Rooms / 4Bedrooms / 3Bath</div><p class="room-desc">Lorem Ipsum is simply dummy text of the printing and typesetting industry.</p><span class="room-more">More Details</span></article>
<article class="room-card" style="left:803px;top:1500px"><div class="room-photo" role="img" aria-label="Photo of a neutral bedroom with artwork above the bed" style="background:linear-gradient(160deg,#d9cdb9,#c2a56a 40%,#ece6dc)"></div><div class="room-strip">25 Harbourview Road, Elmsvale<br>New South Wales<span class="price">$250</span></div><div class="room-meta">▪ 2Guests / 2Rooms / 4Bedrooms / 3Bath</div><p class="room-desc">Lorem Ipsum is simply dummy text of the printing and typesetting industry.</p><span class="room-more">More Details</span></article>

<span class="view-more" style="top:1970px">View More</span>

<section class="feature" role="img" aria-label="Photo of a warmly lit hotel-style bedroom with lamps and a red armchair">
  <div class="feature-card">
    <div class="feature-loc">Australia</div>
    <h3 class="feature-name">Bayside Villas<br>12 Quay Street</h3>
    <div class="feature-amount">$450</div>
    <div class="feature-specs">2 Guests &nbsp;| &nbsp;1 Bedroom &nbsp;| &nbsp;Swimming Pool<br>1 Bed &nbsp;| &nbsp;1.5 Shared baths</div>
    <p class="feature-text">Lorem Ipsum is simply dummy text of<br>the printing and typesetting industry.</p>
    <span class="feature-btn">View More</span>
    <span class="feature-nav">← →</span>
  </div>
</section>

<h2 class="section-title" style="top:2644px">Public Amenities</h2>
<div class="amenity" style="left:73px"><div class="circle"><svg width="40" height="32" viewBox="0 0 40 32"><path d="M6 14l4-10h20l4 10v12H6z" fill="#fff"/><rect x="10" y="8" width="20" height="6" fill="#1474cc"/><circle cx="12" cy="20" r="2.5" fill="#1474cc"/><circle cx="28" cy="20" r="2.5" fill="#1474cc"/></svg></div><h4>Transport</h4><p>Lorem Ipsum is simply a text of the printing has been industry's 1500s...</p><div class="go">→</div></div>
<div class="amenity" style="left:296px"><div class="circle"><svg width="32" height="38" viewBox="0 0 32 38"><rect x="4" y="2" width="24" height="26" rx="5" fill="#fff"/><rect x="8" y="7" width="16" height="8" fill="#1474cc"/><circle cx="10" cy="22" r="2" fill="#1474cc"/><circle cx="22" cy="22" r="2" fill="#1474cc"/><path d="M8 30l-4 6M24 30l4 6" stroke="#fff" stroke-width="3"/></svg></div><h4>Trains</h4><p>Lorem Ipsum is simply a text of the printing has been industry's 1500s...</p><div class="go">→</div></div>
<div class="amenity" style="left:513px"><div class="circle"><svg width="32" height="36" viewBox="0 0 32 36"><rect x="3" y="2" width="26" height="28" rx="4" fill="#fff"/><rect x="7" y="7" width="18" height="10" fill="#1474cc"/><circle cx="9" cy="24" r="2" fill="#1474cc"/><circle cx="23" cy="24" r="2" fill="#1474cc"/><rect x="5" y="30" width="5" height="5" fill="#fff"/><rect x="22" y="30" width="5" height="5" fill="#fff"/></svg></div><h4>Busses</h4><p>Lorem Ipsum is simply a text of the printing has been industry's 1500s...</p><div class="go">→</div></div>
<div class="amenity" style="left:727px"><div class="circle"><svg width="34" height="34" viewBox="0 0 34 34"><circle cx="17" cy="17" r="14" fill="#fff"/><path d="M17 8a6 6 0 0 1 6 6c0 5-6 11-6 11s-6-6-6-11a6 6 0 0 1 6-6z" fill="#1474cc"/><circle cx="17" cy="14" r="2" fill="#fff"/></svg></div><h4>Location</h4><p>Lorem Ipsum is simply a text of the printing has been industry's 1500s...</p><div class="go">→</div></div>
<div class="amenity" style="left:947px"><div class="circle"><svg width="34" height="32" viewBox="0 0 34 32"><rect x="2" y="3" width="30" height="26" fill="none" stroke="#fff" stroke-width="3"/><path d="M8 22l7-8 5 5 6-7" fill="none" stroke="#fff" stroke-width="2.5"/></svg></div><h4>MAP</h4><p>Lorem Ipsum is simply a text of the printing has been industry's 1500s...</p><div class="go">→</div></div>

<h2 class="section-title" style="top:3041px">Our Blogs</h2>
<article class="blog-card" style="left:80px"><div class="blog-photo" role="img" aria-label="Photo of a bedside table with a lamp beside a made bed" style="background:linear-gradient(160deg,#4a5560,#b7b2aa 50%,#e9e4dc)"></div><span class="blog-badge"><svg width="22" height="22"><path d="M9 13l4-4M7 11l-3 3a3 3 0 0 0 4 4l3-3M15 11l3-3a3 3 0 0 0-4-4l-3 3" stroke="#fff" stroke-width="2.2" fill="none"/></svg></span><h4>Blog # 1</h4><span class="blog-date">Aug.10.2018</span><p>Lorem Ipsum is simply dummy text. the printing in the industry and typesetting industry.</p><div class="blog-foot"><span class="read">Read Full Article</span><span class="stat">♡ <b>35</b></span><span class="stat">▭ <b>20</b></span></div></article>
<article class="blog-card" style="left:437px"><div class="blog-photo" role="img" aria-label="Photo of breakfast served on a bed in a sunny room" style="background:linear-gradient(160deg,#c9d9d3,#e8ddd0 50%,#6d93b8)"></div><span class="blog-badge"><svg width="22" height="22"><path d="M9 13l4-4M7 11l-3 3a3 3 0 0 0 4 4l3-3M15 11l3-3a3 3 0 0 0-4-4l-3 3" stroke="#fff" stroke-width="2.2" fill="none"/></svg></span><h4>Blog # 2</h4><span class="blog-date">Aug.09.2018</span><p>Lorem Ipsum is simply dummy text. the printing in the industry and typesetting industry.</p><div class="blog-foot"><span class="read">Read Full Article</span><span class="stat">♡ <b>40</b></span><span class="stat">▭ <b>23</b></span></div></article>
<article class="blog-card" style="left:794px"><div class="blog-photo" role="img" aria-label="Photo of a row of record sleeves in a crate" style="background:linear-gradient(90deg,#2b2b2b,#a33a2e 35%,#d9c7a8 60%,#333)"></div><span class="blog-badge"><svg width="22" height="22"><path d="M9 13l4-4M7 11l-3 3a3 3 0 0 0 4 4l3-3M15 11l3-3a3 3 0 0 0-4-4l-3 3" stroke="#fff" stroke-width="2.2" fill="none"/></svg></span><h4>Blog # 3</h4><span class="blog-date">Aug.8.2018</span><p>Lorem Ipsum is simply dummy text. the printing in the industry and typesetting industry.</p><div class="blog-foot"><span class="read">Read Full Article</span><span class="stat">♡ <b>15</b></span><span class="stat">▭ <b>20</b></span></div></article>

<span class="view-more" style="top:3587px">View More</span>

<h2 class="section-title" style="top:3664px;font-size:25px">Subscribe To Our Newsletter</h2>
<p class="newsletter-sub">To Receive The Latest News And Update</p>
<div class="newsletter-form"><div class="input">Your E-Mail</div><div class="submit">Submit</div></div>

<footer class="site-footer">
  <div class="f-col" style="left:63px">
    <div class="f-brand"><span class="brand-dot"></span><div><div class="brand-name">Lodgivo</div><div class="brand-tag" style="color:#ddd">Executive Accommodation</div></div></div>
    <p class="f-about">Lorem Ipsum is simply dummy text of the printing and types tysetting industry...</p>
    <div class="socials"><span></span><span></span><span></span><span></span><span></span></div>
  </div>
  <div class="f-col" style="left:371px">
    <h4>Useful links</h4>
    <ul class="links"><li>› Login</li><li>› Register</li><li>› My Profile</li><li>› My Subscription</li><li>› Privacy policy</li><li>› Terms &amp; Conditions</li></ul>
  </div>
  <div class="f-col" style="left:603px">
    <h4>Contact us</h4>
    <div class="contact-row"><svg width="14" height="14"><polygon points="7,1 13,7 11,7 11,13 3,13 3,7 1,7" fill="#ddd"/></svg><span>14 Wattle Court ,Brindlemere<br>Western Australia.<br>ZipCode: 12345</span></div>
    <div class="contact-row"><svg width="14" height="14"><path d="M3 1h3l1 3-2 1.5a8 8 0 0 0 3.5 3.5L10 7l3 1v3c0 1-1 2-2 2A11 11 0 0 1 1 3c0-1 1-2 2-2z" fill="#ddd"/></svg><span>123 555 0190</span></div>
    <div class="contact-row"><svg width="14" height="14"><rect x="1" y="3" width="12" height="9" fill="none" stroke="#ddd" stroke-width="1.5"/><path d="M1 3l6 5 6-5" fill="none" stroke="#ddd" stroke-width="1.5"/></svg><span>info@Lodgivo.com</span></div>
  </div>
  <div class="f-col" style="left:906px">
    <h4>Quick Contact</h4>
    <div class="qc-row"><div class="qc-field" style="width:114px">Name</div><div class="qc-field" style="width:118px">Phone</div></div>
    <div class="qc-field" style="width:236px;height:62px;margin-top:6px;align-items:flex-start;padding-top:8px">Message</div>
    <div class="qc-send">Send</div>
  </div>
</footer>

<div class="bottom-bar">CopyRight © 2019 Lodgivo. All Right Reserve
  <div class="cards"><span></span><span></span><span></span><span></span><span></span></div>
</div>

</body>
</html>
```